A specialised Sport management needs a corporate brochure design

We are a specialized company in the management and consultancy of sports events. and need to have a company brochure
We provide the following services;
Event management
Venues management
Production
Ticketing
Consulting
Hospitality
Activity management
Event timing
Branding of event
Event supplies
We need a corporate profile design for our company to showcase the major events that we have covered , with images, information, statistics, surveys, products and services used. We want to highlight our professionalism and execution of the events, experience of the participants, spectators . How we have grown in the past few years and reached the international standards.
Objectives of the work:
To get sponsors and partners for future business and to present Tri-Crest
as not just a sports management company but also a professional sports
events management company.
You can check our website
www.tri-crest.example
Target Market(s)
Sponsors and corporate partners
Industry/Entity Type
Events
Requirements
Must have
- Must Have:
- - Very professional look
- -Some event images,Event information, statistics, surveys, products and services used. We want to highlight our professionalism and execution of the events (Attached)
Nice to have
- Similar momentom of the below design
- http://www.lumavent.example/wp-content/themes/lumavent/pdf/CP-2014-15-V10-Web.pdf

```html
<!DOCTYPE html>
<html lang="en">
<head>
<meta charset="utf-8">
<title>Tri-Crest Corporate Brochure – Services Spread</title>
<link rel="stylesheet" href="https://fonts.googleapis.com/css2?family=Exo+2:wght@300;400;500&display=swap">
<style>
  :root {
    --backdrop: #e9e7e4;
    --paper: #ffffff;
    --paper-shade: #e4e5e8;
    --ink: #5d5f63;
    --ink-soft: #7a7c80;
    --heading: #4f5156;
    --orange: #e8683e;
    --orange-line: #f29a7a;
    --green: #2f9a63;
    --slate: #7d8189;
    --icon-grey: #a9acb1;
    --photo-green: #5f7a4f;
    --photo-stone: #cfc6b1;
  }
  * { box-sizing: border-box; margin: 0; padding: 0; }
  html, body { width: 1200px; height: 900px; overflow: hidden; }
  body {
    background: var(--backdrop);
    font-family: "Exo 2", sans-serif;
    color: var(--ink);
    position: relative;
  }
  .spread {
    position: absolute; left: 50px; top: 140px;
    width: 1100px; height: 620px;
    display: flex;
    box-shadow: 0 10px 30px rgba(0,0,0,.18);
  }
  .page { position: relative; width: 550px; height: 620px; overflow: hidden; }

  /* Left page */
  .page--photo { background: var(--paper); }
  .event-photo {
    position: absolute; inset: 0;
    background: linear-gradient(100deg, var(--photo-green) 0%, var(--photo-stone) 100%);
  }
  .photo-bands { position: absolute; left: 0; bottom: 0; width: 550px; height: 70px; }

  /* Right page */
  .page--services {
    background: linear-gradient(180deg, var(--paper) 0%, #f4f4f6 60%, var(--paper-shade) 100%);
    padding: 26px 28px 0 30px;
  }
  .section-title {
    font-weight: 300; font-size: 27px; color: var(--heading);
    letter-spacing: .2px; line-height: 1.1; margin-bottom: 6px;
  }
  .section-body { font-size: 8.6px; line-height: 1.45; color: var(--ink-soft); margin-bottom: 16px; }
  .service-list { list-style: none; margin: 3px 0 2px; }
  .service-list li::before { content: "– "; }

  .stats {
    position: absolute; left: 0; bottom: 0;
    width: 340px; height: 140px;
    background: var(--orange);
    display: grid; grid-template-columns: repeat(3, 1fr); grid-template-rows: 1fr 1fr;
    color: #fff;
  }
  .stat {
    padding: 6px 8px; text-align: center;
    border-right: 1px solid var(--orange-line);
    border-bottom: 1px solid var(--orange-line);
    display: flex; flex-direction: column; justify-content: space-between;
  }
  .stat:nth-child(3n) { border-right: none; }
  .stat:nth-child(n+4) { border-bottom: none; }
  .stat__label { font-size: 7.6px; line-height: 1.2; }
  .stat__value { font-size: 20px; font-weight: 400; line-height: 1.1; }

  .growth {
    position: absolute; left: 350px; bottom: 14px; width: 190px;
  }
  .growth__title { font-size: 15px; font-weight: 500; color: var(--heading); margin-bottom: 8px; }
  .growth__row { display: flex; align-items: center; gap: 5px; height: 24px; }
  .year-tag {
    width: 32px; height: 12px; background: var(--green); color: #fff;
    font-size: 7px; line-height: 12px; padding-left: 4px; flex: none;
    clip-path: polygon(0 0, 80% 0, 100% 50%, 80% 100%, 0 100%);
  }
  .growth__meta { width: 150px; }
  .growth__label { font-size: 7.5px; color: var(--ink); display: block; line-height: 1.2; }
  .people { display: block; width: 150px; height: 11px; }
  .person--on { fill: var(--orange); }
  .person--off { fill: var(--icon-grey); }
</style>
</head>
<body>
<svg width="0" height="0" style="position:absolute">
  <defs>
    <symbol id="person" viewBox="0 0 8 12">
      <circle cx="4" cy="2" r="1.8"/>
      <path d="M1.5 4.5h5v4h-1v3.5h-3V8.5h-1z"/>
    </symbol>
  </defs>
</svg>

<main class="spread">
  <section class="page page--photo">
    <div class="event-photo" role="img" aria-label="Photo of a young climber on an outdoor climbing wall surrounded by trees"></div>
    <svg class="photo-bands" viewBox="0 0 550 70" aria-hidden="true">
      <polygon points="0,16 360,16 336,40 0,40" fill="#2f9a63"/>
      <polygon points="372,10 550,20 550,40 352,30" fill="#e8683e"/>
      <rect x="0" y="40" width="550" height="30" fill="#7d8189"/>
    </svg>
  </section>

  <section class="page page--services">
    <h2 class="section-title">Consultancy Services</h2>
    <div class="section-body">
      <p>Tri-Crest is a team of professionals with a proven track record in the field. We guide and assist you in every stage of your project, from tournaments and championships to outdoor and indoor events. Each event is different and has different needs, so our consultants bring a wide range of expertise to every brief, such as:</p>
      <ul class="service-list">
        <li>Event planning and safety</li>
        <li>Licensing and permissions</li>
        <li>Staff support services</li>
        <li>Technical setup</li>
        <li>Budget and sponsorship</li>
      </ul>
      <p>Please do not hesitate to contact us for further information.</p>
    </div>

    <h2 class="section-title">Event Management</h2>
    <p class="section-body">Tri-Crest Sports Management has unique specialist experience in the creation and organisation of sporting events, both local and regional. During the last seven years we have developed a considerable variety of events such as marathons, futsal tournaments, kart competitions and summer camps. We use the latest technology available to ensure the best quality service for our clients.</p>

    <h2 class="section-title">Facility Management</h2>
    <p class="section-body">Tri-Crest is a leader in venue management, financing and development, from stadiums and arenas around Kuwait and the region. Through our business energy we create the right environment for every sport facility to reach the highest return. We provide a complete solution for sporting federations, professional teams, schools, colleges and universities, including business planning and general admission ticketing.</p>

    <div class="stats">
      <div class="stat"><span class="stat__label">Number of participants in 2014</span><span class="stat__value">10,000</span></div>
      <div class="stat"><span class="stat__label">Number of sports</span><span class="stat__value">13</span></div>
      <div class="stat"><span class="stat__label">Visitors</span><span class="stat__value">+30,000</span></div>
      <div class="stat"><span class="stat__label">Said they would rate our event as “Excellent” (average)</span><span class="stat__value">86%</span></div>
      <div class="stat"><span class="stat__label">Said they would participate again (average)</span><span class="stat__value">84%</span></div>
      <div class="stat"><span class="stat__label">Said they recognised our sponsors (average)</span><span class="stat__value">80%</span></div>
    </div>

    <div class="growth">
      <h3 class="growth__title">Growth Over the Years</h3>

      <div class="growth__row">
        <span class="year-tag">2011</span>
        <div class="growth__meta">
          <span class="growth__label">Participants 1,200</span>
          <svg class="people" viewBox="0 0 150 11" aria-hidden="true">
            <use href="#person" x="0" width="8" height="11" class="person--on"/><use href="#person" x="9" width="8" height="11" class="person--on"/>
            <use href="#person" x="18" width="8" height="11" class="person--off"/><use href="#person" x="27" width="8" height="11" class="person--off"/><use href="#person" x="36" width="8" height="11" class="person--off"/><use href="#person" x="45" width="8" height="11" class="person--off"/><use href="#person" x="54" width="8" height="11" class="person--off"/><use href="#person" x="63" width="8" height="11" class="person--off"/><use href="#person" x="72" width="8" height="11" class="person--off"/><use href="#person" x="81" width="8" height="11" class="person--off"/><use href="#person" x="90" width="8" height="11" class="person--off"/><use href="#person" x="99" width="8" height="11" class="person--off"/><use href="#person" x="108" width="8" height="11" class="person--off"/><use href="#person" x="117" width="8" height="11" class="person--off"/><use href="#person" x="126" width="8" height="11" class="person--off"/><use href="#person" x="135" width="8" height="11" class="person--off"/>
          </svg>
        </div>
      </div>

      <div class="growth__row">
        <span class="year-tag">2012</span>
        <div class="growth__meta">
          <span class="growth__label">Participants 2,700</span>
          <svg class="people" viewBox="0 0 150 11" aria-hidden="true">
            <use href="#person" x="0" width="8" height="11" class="person--on"/><use href="#person" x="9" width="8" height="11" class="person--on"/><use href="#person" x="18" width="8" height="11" class="person--on"/><use href="#person" x="27" width="8" height="11" class="person--on"/>
            <use href="#person" x="36" width="8" height="11" class="person--off"/><use href="#person" x="45" width="8" height="11" class="person--off"/><use href="#person" x="54" width="8" height="11" class="person--off"/><use href="#person" x="63" width="8" height="11" class="person--off"/><use href="#person" x="72" width="8" height="11" class="person--off"/><use href="#person" x="81" width="8" height="11" class="person--off"/><use href="#person" x="90" width="8" height="11" class="person--off"/><use href="#person" x="99" width="8" height="11" class="person--off"/><use href="#person" x="108" width="8" height="11" class="person--off"/><use href="#person" x="117" width="8" height="11" class="person--off"/><use href="#person" x="126" width="8" height="11" class="person--off"/><use href="#person" x="135" width="8" height="11" class="person--off"/>
          </svg>
        </div>
      </div>

      <div class="growth__row">
        <span class="year-tag">2013</span>
        <div class="growth__meta">
          <span class="growth__label">Participants 5,600+</span>
          <svg class="people" viewBox="0 0 150 11" aria-hidden="true">
            <use href="#person" x="0" width="8" height="11" class="person--on"/><use href="#person" x="9" width="8" height="11" class="person--on"/><use href="#person" x="18" width="8" height="11" class="person--on"/><use href="#person" x="27" width="8" height="11" class="person--on"/><use href="#person" x="36" width="8" height="11" class="person--on"/><use href="#person" x="45" width="8" height="11" class="person--on"/><use href="#person" x="54" width="8" height="11" class="person--on"/><use href="#person" x="63" width="8" height="11" class="person--on"/><use href="#person" x="72" width="8" height="11" class="person--on"/>
            <use href="#person" x="81" width="8" height="11" class="person--off"/><use href="#person" x="90" width="8" height="11" class="person--off"/><use href="#person" x="99" width="8" height="11" class="person--off"/><use href="#person" x="108" width="8" height="11" class="person--off"/><use href="#person" x="117" width="8" height="11" class="person--off"/><use href="#person" x="126" width="8" height="11" class="person--off"/><use href="#person" x="135" width="8" height="11" class="person--off"/>
          </svg>
        </div>
      </div>

      <div class="growth__row">
        <span class="year-tag">2014</span>
        <div class="growth__meta">
          <span class="growth__label">Participants 10,000+</span>
          <svg class="people" viewBox="0 0 150 11" aria-hidden="true">
            <use href="#person" x="0" width="8" height="11" class="person--on"/><use href="#person" x="9" width="8" height="11" class="person--on"/><use href="#person" x="18" width="8" height="11" class="person--on"/><use href="#person" x="27" width="8" height="11" class="person--on"/><use href="#person" x="36" width="8" height="11" class="person--on"/><use href="#person" x="45" width="8" height="11" class="person--on"/><use href="#person" x="54" width="8" height="11" class="person--on"/><use href="#person" x="63" width="8" height="11" class="person--on"/><use href="#person" x="72" width="8" height="11" class="person--on"/><use href="#person" x="81" width="8" height="11" class="person--on"/><use href="#person" x="90" width="8" height="11" class="person--on"/><use href="#person" x="99" width="8" height="11" class="person--on"/><use href="#person" x="108" width="8" height="11" class="person--on"/><use href="#person" x="117" width="8" height="11" class="person--on"/><use href="#person" x="126" width="8" height="11" class="person--on"/><use href="#person" x="135" width="8" height="11" class="person--on"/>
          </svg>
        </div>
      </div>
    </div>
  </section>
</main>
</body>
</html>
```